New business card/stationary for a consulting company

I am looking for a clean and very professional looking business card for my consulting company as well as corresponding stationary. I am uploading our logo. I like simple and powerful for the feel. No graphics but I am open on everything else. Below is my contact information but would like the final to be in a version I can add my employees information into and print. Thank you.

Daniel Whitcombe
dan@ferncliffadvisory.com
2870 North 9th Avenue, Summit Floor, Elm Ridge, Illinois 60531
www.ferncliffadvisory.com

Industry/Entity Type

Consulting

Contact Information for Business Card

Daniel Whitcombe
dan@ferncliffadvisory.com
www.ferncliffadvisory.com

Font styles to use
Serif
Sans Serif

Requirements
Must have
• Our logo and the business card details.
Nice to have
• our website www.ferncliffadvisory.com

```html
<!DOCTYPE html>
<html lang="en">
<head>
<meta charset="utf-8">
<title>Ferncliff Advisory – Business Card</title>
<link rel="stylesheet" href="https://fonts.googleapis.com/css2?family=Cinzel:wght@700&family=Roboto:wght@400;500;700&family=Montserrat:wght@400&display=swap">
<style>
  :root {
    --navy: #0c0c7a;
    --navy-deep: #05055e;
    --royal: #0a0a9a;
    --band: #0a0a90;
    --paper: #f3f3f3;
    --ink-grey: #555555;
    --rule-grey: #b8b8b8;
    --band-grey: #c4c4c4;
    --backdrop: #e6e3de;
    --white: #ffffff;
    --silver: #e8e8ee;
  }
  * { margin: 0; padding: 0; box-sizing: border-box; }
  html, body { width: 1200px; height: 960px; overflow: hidden; }
  body { background: var(--backdrop); position: relative; font-family: "Roboto", Arial, sans-serif; }

  .card { position: absolute; width: 600px; height: 342px; box-shadow: 0 3px 8px rgba(0,0,0,0.25); overflow: hidden; }
  .card--front { left: 302px; top: 130px; background: var(--paper); }
  .card--back { left: 300px; top: 488px; background: linear-gradient(100deg, var(--royal) 0%, var(--navy) 50%, var(--navy-deep) 100%); }

  .brand { position: absolute; display: flex; flex-direction: column; align-items: center; }
  .brand__square { width: 46px; height: 46px; }
  .brand__name { font-family: "Montserrat", Arial, sans-serif; font-weight: 400; white-space: nowrap; letter-spacing: 0.5px; }

  .card--front .brand { right: 40px; top: 40px; width: 290px; }
  .card--front .brand__square { background: var(--navy); margin-bottom: 16px; }
  .card--front .brand__name { font-size: 21px; color: var(--navy); }

  .card--back .brand { left: 0; right: 0; top: 116px; }
  .card--back .brand__square { background: var(--silver); margin-bottom: 22px; }
  .card--back .brand__name { font-size: 30px; color: var(--silver); }

  .person__accent { position: absolute; left: 0; top: 183px; width: 8px; height: 40px; background: var(--navy); }
  .person__name { position: absolute; left: 31px; top: 181px; font-family: "Cinzel", Georgia, serif; font-weight: 700; font-size: 20px; color: var(--navy); letter-spacing: 0.3px; }
  .person__email { position: absolute; left: 32px; top: 206px; font-size: 14px; color: var(--ink-grey); }
  .divider { position: absolute; left: 32px; top: 234px; width: 528px; height: 1px; background: var(--rule-grey); }
  .address { position: absolute; left: 32px; top: 246px; font-size: 14px; line-height: 18px; color: var(--ink-grey); font-style: normal; }

  .footer-band { position: absolute; left: 0; bottom: 0; width: 600px; height: 28px; display: block; }
  .website { position: absolute; right: 18px; bottom: 0; height: 28px; line-height: 28px; font-size: 13px; font-weight: 500; color: var(--white); letter-spacing: 1px; }
</style>
</head>
<body>
  <section class="card card--front">
    <div class="brand">
      <div class="brand__square"></div>
      <div class="brand__name">FERNCLIFF ADVISORY</div>
    </div>

    <div class="person__accent"></div>
    <h1 class="person__name">Daniel Whitcombe</h1>
    <p class="person__email">dan@ferncliffadvisory.com</p>
    <div class="divider"></div>
    <address class="address">
      2870 North 9th Avenue<br>
      Summit Floor, Elm Ridge<br>
      Illinois 60531
    </address>

    <svg class="footer-band" viewBox="0 0 600 28" aria-hidden="true">
      <path d="M0 10 H314 Q320 10 318 13 Q316 16 310 16 H0 Z" fill="#c4c4c4"/>
      <path d="M0 18 H305 Q315 18 320 12 L326 5 Q331 0 340 0 H600 V28 H0 Z" fill="#0a0a90"/>
    </svg>
    <span class="website">WWW.FERNCLIFFADVISORY.COM</span>
  </section>

  <section class="card card--back">
    <div class="brand">
      <div class="brand__square"></div>
      <div class="brand__name">FERNCLIFF ADVISORY</div>
    </div>
  </section>
</body>
</html>
```